KBT Business Cards

We require business cards for our business. We would like a matte black back to the card, with our logo centred in the middle. The front side of the card is open to design.

Target Market(s)

Clients looking for legal services (professional)

Industry/Entity Type

Legal

Contact Information for Business Card

Doran Kelbrath
Partner
Mobile: 0461 738 524
Email: doran@kbtlaw.co
Website: www.kbtlaw.co
Level 3, 118 Wendmore Street
Sydney NSW 2000

Font styles to use
Other font styles liked:
• Avenir

Colors
f04a50
ffffff
1b1b1b

Requirements
Must have
• Black back with logo included in the centre of the card.
• Our font is Avenir.

```html
<!DOCTYPE html>
<html lang="en">
<head>
<meta charset="utf-8">
<title>KBT Legal — Business Card</title>
<link rel="stylesheet" href="https://fonts.googleapis.com/css2?family=Mulish:wght@300;400;600;800&display=swap">
<style>
  :root {
    --page: #e9e7e4;
    --card-light-top: #f7f6f4;
    --card-light-bottom: #dedddb;
    --ink: #1b1b1b;
    --red: #f04a50;
    --red-deep: #a3192b;
    --red-dark: #7c0d1a;
    --black-top: #3a3a3a;
    --black-bottom: #111111;
    --contact-text: #d9d6d6;
    --white: #ffffff;
  }
  * { box-sizing: border-box; margin: 0; padding: 0; }
  html, body {
    width: 1200px; height: 970px; overflow: hidden;
    background: var(--page);
    font-family: "Mulish", "Avenir", sans-serif;
  }
  .business-card {
    position: absolute; left: 80px; top: 188px;
    width: 1040px; height: 594px;
    background: linear-gradient(180deg, var(--card-light-top), var(--card-light-bottom));
    box-shadow: 0 18px 40px rgba(0,0,0,0.18);
    overflow: hidden;
  }
  .brand {
    position: absolute; left: 48px; top: 140px;
    display: flex; align-items: center; gap: 26px;
  }
  .brand-square {
    width: 54px; height: 54px; background: var(--red-deep);
  }
  .brand-name {
    font-weight: 800; font-size: 50px; letter-spacing: 1px;
    color: var(--ink); line-height: 1;
  }
  .title-band {
    position: absolute; left: 0; top: 312px; width: 100%; height: 60px;
    background: linear-gradient(90deg, var(--red-deep) 0%, #8e1322 55%, var(--red-dark) 100%);
    border-bottom: 3px solid #e8d9da;
    display: flex; align-items: center; padding-left: 48px;
  }
  .person-name {
    font-weight: 600; font-size: 26px; letter-spacing: 1px;
    color: #f3e6e7; text-transform: uppercase;
  }
  .band-divider {
    width: 2px; height: 36px; background: #f3e6e7; margin: 0 26px;
  }
  .person-role {
    font-weight: 400; font-size: 23px; letter-spacing: 1px; color: #f3e6e7;
  }
  .contact-panel {
    position: absolute; left: 0; top: 375px; width: 100%; bottom: 0;
    background: linear-gradient(180deg, var(--black-top), var(--black-bottom));
    padding: 58px 0 0 48px;
  }
  .contact-row {
    display: flex; align-items: center; height: 40px;
    font-weight: 300; font-size: 24px; letter-spacing: 0.5px;
    color: var(--contact-text);
  }
  .contact-item { display: flex; align-items: center; }
  .contact-icon { width: 30px; height: 30px; margin-right: 14px; flex: none; }
  .contact-sep {
    width: 2px; height: 26px; background: var(--contact-text); margin: 0 22px;
  }
</style>
</head>
<body>
  <main class="business-card">
    <div class="brand">
      <div class="brand-square"></div>
      <div class="brand-name">KBT LEGAL</div>
    </div>

    <div class="title-band">
      <span class="person-name">Doran Kelbrath</span>
      <span class="band-divider"></span>
      <span class="person-role">Partner</span>
    </div>

    <section class="contact-panel">
      <div class="contact-row">
        <span class="contact-item">
          <svg class="contact-icon" viewBox="0 0 30 30" aria-hidden="true">
            <circle cx="15" cy="15" r="13" fill="none" stroke="#c8303c" stroke-width="2.5"/>
            <circle cx="15" cy="15" r="9.5" fill="#c8303c"/>
            <rect x="11" y="9" width="8" height="12" rx="1.5" fill="none" stroke="#2a2a2a" stroke-width="1.8"/>
          </svg>
          0461 738 524
        </span>
        <span class="contact-sep"></span>
        <span class="contact-item">
          <svg class="contact-icon" viewBox="0 0 30 30" aria-hidden="true">
            <circle cx="15" cy="15" r="13" fill="none" stroke="#c8303c" stroke-width="2.5"/>
            <circle cx="15" cy="15" r="9.5" fill="#c8303c"/>
            <rect x="9.5" y="11" width="11" height="8" fill="none" stroke="#2a2a2a" stroke-width="1.6"/>
            <path d="M9.5 11 L15 15.5 L20.5 11" fill="none" stroke="#2a2a2a" stroke-width="1.6"/>
          </svg>
          doran@kbtlaw.co
        </span>
      </div>
      <div class="contact-row">
        <span class="contact-item">
          <svg class="contact-icon" viewBox="0 0 30 30" aria-hidden="true">
            <circle cx="15" cy="15" r="13" fill="none" stroke="#c8303c" stroke-width="2.5"/>
            <circle cx="15" cy="15" r="9.5" fill="#c8303c"/>
            <circle cx="15" cy="15" r="6" fill="none" stroke="#2a2a2a" stroke-width="1.4"/>
            <ellipse cx="15" cy="15" rx="2.6" ry="6" fill="none" stroke="#2a2a2a" stroke-width="1.2"/>
            <path d="M9 15 H21" stroke="#2a2a2a" stroke-width="1.2"/>
          </svg>
          www.kbtlaw.co
        </span>
      </div>
      <div class="contact-row">
        <span class="contact-item">
          <svg class="contact-icon" viewBox="0 0 30 30" aria-hidden="true">
            <circle cx="15" cy="15" r="13" fill="none" stroke="#c8303c" stroke-width="2.5"/>
            <circle cx="15" cy="15" r="9.5" fill="#c8303c"/>
            <path d="M15 22 C11 17 10.5 15 10.5 13.5 A4.5 4.5 0 0 1 19.5 13.5 C19.5 15 19 17 15 22 Z" fill="#2a2a2a"/>
            <circle cx="15" cy="13.5" r="1.6" fill="#c8303c"/>
          </svg>
          Level 3, 118 Wendmore Street. Sydney NSW 2000
        </span>
      </div>
    </section>
  </main>
</body>
</html>
```